Alaska Law Firm Needs a Sticker Design

We need a design for stickers to put on already-printed brochures. We mail the brochures to potential clients so they can learn more about accident-induced injuries, insurance claims, legal representation, and our own law firm.

One of our lawyers wrote a book that provides a helpful overview of personal injury claims. We are offering this book for free to anyone who calls and requests it. Therefore, the sticker design should include one of the following phrases, or something very similar:
a) "Still have questions? Call and request our book-- for free!"
b) "Still have questions about auto accident claims? Call and request our book today."
c) "Still have questions about filing a claim? Call and request a free copy of our book."
d) "Still have questions? Call us today to request a free copy of our book, Clear Lanes Ahead."
e) "To learn more about automobile accidents and insurance, call today and request a free copy of our book."

The sticker should be approximately 3"x3" and may be a circle, square, rectangle, or ellipsis. The sticker will be placed on the back of the folder, which is light blue. We would like the sticker to match the color scheme of our website and the folder.

I will upload an image of the book cover as soon as I obtain it.

Law Firm

Font styles to use
Serif
Sans Serif

Requirements
Should not have
• Bright colors that aren't already used in the folder design. e.g. no bright orange, pink, chartreuse, turquoise, yellow, red.

```html
<!DOCTYPE html>
<html lang="en">
<head>
<meta charset="utf-8">
<title>Still Have Questions – Free Book Sticker</title>
<link href="https://fonts.googleapis.com/css2?family=Bebas+Neue&family=Open+Sans:wght@400;600;700&display=swap" rel="stylesheet">
<style>
  :root {
    --page-bg: #e9e9e9;
    --navy: #143f6b;
    --navy-ink: #173a63;
    --white: #ffffff;
    --cover-edge: #c9ccd1;
    --photo-sky: #b9d3e6;
    --photo-field: #6ea447;
  }
  html, body {
    margin: 0;
    padding: 0;
    width: 1200px;
    height: 855px;
    overflow: hidden;
    background: var(--page-bg);
  }
  .sticker { display: block; width: 1200px; height: 855px; }
  .headline { font-family: "Bebas Neue", "Oswald", sans-serif; fill: var(--white); }
  .headline--big { font-size: 131px; }
  .headline--spaced { font-size: 74px; letter-spacing: 17px; }
  .headline--free { font-size: 154px; }
  .offer-line { font-family: "Bebas Neue", "Oswald", sans-serif; font-size: 48px; fill: var(--navy-ink); }
  .phone-line { font-family: "Open Sans", Arial, sans-serif; font-weight: 600; font-size: 54px; fill: var(--navy-ink); }
  .book-author { font-family: "Open Sans", Arial, sans-serif; font-size: 11px; fill: #333a44; }
  .book-title { font-family: "Open Sans", Arial, sans-serif; font-weight: 700; font-size: 21px; fill: var(--navy-ink); }
  .book-subtitle { font-family: "Open Sans", Arial, sans-serif; font-size: 7.5px; fill: var(--white); letter-spacing: 0.3px; }
</style>
</head>
<body>
<svg class="sticker" viewBox="0 0 1200 855" xmlns="http://www.w3.org/2000/svg">
  <defs>
    <clipPath id="sticker-face">
      <circle cx="600" cy="428" r="330"/>
    </clipPath>
    <linearGradient id="cover-photo-tones" x1="0" y1="0" x2="0" y2="1">
      <stop offset="0" stop-color="var(--photo-sky)"/>
      <stop offset="0.45" stop-color="#8fbf6a"/>
      <stop offset="1" stop-color="var(--photo-field)"/>
    </linearGradient>
  </defs>

  <!-- sticker body -->
  <circle class="sticker-rim" cx="600" cy="428" r="338" fill="var(--white)"/>
  <g clip-path="url(#sticker-face)">
    <rect class="sticker-fill" x="262" y="90" width="676" height="676" fill="var(--navy)"/>
    <rect class="offer-band" x="262" y="402" width="676" height="170" fill="var(--white)"/>
  </g>

  <!-- headline -->
  <text class="headline headline--big" x="600" y="274" text-anchor="middle">STILL HAVE</text>
  <text class="headline headline--spaced" x="608" y="350" text-anchor="middle">QUESTIONS?</text>

  <!-- offer -->
  <text class="offer-line" x="486" y="474" text-anchor="middle">CALL &amp; REQUEST OUR BOOK</text>
  <text class="phone-line" x="496" y="533" text-anchor="middle">(907) 555-0142</text>

  <!-- book -->
  <g class="book" transform="rotate(3 780 490)">
    <rect class="book-spine-edge" x="855" y="368" width="8" height="252" fill="var(--cover-edge)"/>
    <rect class="book-cover" x="698" y="362" width="160" height="256" fill="var(--white)" stroke="#d6d8dc" stroke-width="1"/>
    <text class="book-author" x="778" y="384" text-anchor="middle">DANIEL R. HARTLEY</text>
    <text class="book-title" x="778" y="410" text-anchor="middle">CLEAR LANES</text>
    <text class="book-title" x="778" y="432" text-anchor="middle">AHEAD</text>
    <rect class="book-photo" x="704" y="440" width="148" height="142" fill="url(#cover-photo-tones)"
          role="img" aria-label="Cover photo of a smiling family lying on grass beside a small red car"/>
    <rect class="book-footer" x="704" y="582" width="148" height="32" fill="var(--navy)"/>
    <text class="book-subtitle" x="778" y="596" text-anchor="middle">THE RIGHT WAY TO HANDLE</text>
    <text class="book-subtitle" x="778" y="607" text-anchor="middle">YOUR AUTO ACCIDENT CLAIM</text>
  </g>

  <!-- free -->
  <text class="headline headline--free" x="604" y="710" text-anchor="middle">FREE !!</text>
</svg>
</body>
</html>
```